Brochure for a website accessibility report

This brochure is related to a report that www.qelvantrix.org sell. The report shows the results of an automated audit of a websites accessibility. It shows details of issues found with screen shots, examples of code and provides remediation advice.

The brochure will be a pdf 8.5 inches by 11 inches. It can be anywhere from 6 to 10 pages.

The FlintVue™ name itself should be “Bree Serif” font. The fonts, styles, colors and sizes are up to you.

The images used and logo of the Office of Digital Reachworks and K7P logo are upload

We highlighted in blue page extracts from the report we sell. Do not use the blue highlight, it is merely there to show you where the specific examples of the report we sell are vs the other content in the report. The areas in blue which show the content from the actual report should be shown as an extract of the actual page of the report. You have flexibility to change the layout and the way the content look.

The red square callouts over the blue content are callouts that describe the specific page extracts. We used it as a red callout only so that you would be able to see it. You should change the specific location, look and feel of the callout to be appropriate

Target Market(s)

Marketing and Technical people

Industry/Entity Type

Information Technology

Font styles to use
Sans Serif

Colors

Designer to choose colors to be used in the design.

Requirements
Should not have
• wheelchairs, images of blind people

```html
<!DOCTYPE html>
<html lang="en">
<head>
<meta charset="utf-8">
<title>Office of Digital Reachworks — Report Brochure Covers</title>
<link rel="stylesheet" href="https://fonts.googleapis.com/css2?family=Bree+Serif&family=Montserrat:wght@400;500;600&display=swap">
<style>
  :root {
    --backdrop: #a3a4a8;
    --paper: #f1f1f1;
    --paper-edge: #e2e2e3;
    --band: #474748;
    --green-light: #52c28f;
    --green: #33ad6f;
    --green-deep: #279c5f;
    --white: #ffffff;
    --ink: #6b6b6e;
    --accent: #3fb47c;
  }
  * { box-sizing: border-box; margin: 0; padding: 0; }
  html, body {
    width: 1200px;
    height: 900px;
    overflow: hidden;
    background: var(--backdrop);
  }
  .spread {
    position: absolute;
    left: 106px;
    top: 130px;
    width: 988px;
    height: 640px;
    display: flex;
    box-shadow: 0 14px 36px rgba(0, 0, 0, 0.28);
  }
  .page {
    position: relative;
    width: 494px;
    height: 640px;
    overflow: hidden;
  }

  /* Back cover */
  .back-cover {
    background: linear-gradient(90deg, var(--paper) 0%, var(--paper) 86%, var(--paper-edge) 100%);
  }
  .back-cover__band {
    position: absolute;
    left: 120px;
    right: 0;
    top: 268px;
    height: 86px;
    background: var(--band);
  }
  .contact {
    position: absolute;
    left: 120px;
    top: 498px;
    font-family: "Montserrat", sans-serif;
    font-style: normal;
    color: var(--ink);
  }
  .contact__title {
    font-size: 13px;
    font-weight: 500;
    letter-spacing: 0.32em;
    color: var(--accent);
    margin-bottom: 6px;
  }
  .contact__lines {
    font-size: 8.5px;
    line-height: 1.45;
  }
  .contact__lines + .contact__lines { margin-top: 9px; }
  .back-cover__web {
    position: absolute;
    right: 40px;
    top: 516px;
    font-family: "Montserrat", sans-serif;
    font-size: 8.5px;
    color: var(--accent);
  }

  /* Front cover */
  .front-cover {
    background: linear-gradient(100deg, var(--green-light) 0%, var(--green) 45%, var(--green-deep) 100%);
    color: var(--white);
  }
  .front-cover__spine-shade {
    position: absolute;
    inset: 0 auto 0 0;
    width: 40px;
    background: linear-gradient(90deg, rgba(255,255,255,0.28), rgba(255,255,255,0));
  }
  .brand {
    position: absolute;
    left: 64px;
    top: 276px;
    display: flex;
    align-items: center;
    gap: 8px;
  }
  .brand__dot {
    width: 10px;
    height: 10px;
    border-radius: 50%;
    background: var(--white);
  }
  .brand__name {
    font-family: "Montserrat", sans-serif;
    font-size: 12px;
    font-weight: 500;
    letter-spacing: 0.04em;
    color: var(--white);
  }
  .report-title {
    position: absolute;
    left: 64px;
    top: 318px;
    font-family: "Bree Serif", serif;
    font-size: 40px;
    font-weight: 400;
    letter-spacing: 0.1em;
    line-height: 1;
  }
  .report-subtitle {
    position: absolute;
    left: 66px;
    top: 364px;
    font-family: "Montserrat", sans-serif;
    font-size: 6.5px;
    font-weight: 600;
    letter-spacing: 0.3em;
    text-transform: uppercase;
  }
</style>
</head>
<body>
  <main class="spread">
    <section class="page back-cover" aria-label="Back cover">
      <div class="back-cover__band"></div>
      <address class="contact">
        <p class="contact__title">CONTACT</p>
        <p class="contact__lines">
          Headquarters<br>
          Office of Digital Reachworks<br>
          410 Corrow Lane Suite 88<br>
          Halvenby, NT 40917
        </p>
        <p class="contact__lines">
          Phone: 555-014-2290<br>
          Email us: hello@qelvantrix.org
        </p>
      </address>
      <p class="back-cover__web">www.qelvantrix.org</p>
    </section>

    <section class="page front-cover" aria-label="Front cover">
      <div class="front-cover__spine-shade"></div>
      <div class="brand">
        <span class="brand__dot"></span>
        <p class="brand__name">Office of Digital Reachworks</p>
      </div>
      <h1 class="report-title">REPORT</h1>
      <p class="report-subtitle">Office of Digital Reachworks</p>
    </section>
  </main>
</body>
</html>
```